BRANDEMEIER & BRANDEMEIER,LLP NEEDS A NEW LETTERHEAD DESIGN

a conservative yet contemporary layout befitting a long established
firm, consistent with the times, some form of logo so it catches ones attention, and is
admirable, but portrays integrity
Updates

I would like to approve #22066987 Please advise how to do this as it’s confusing on the site so I can approve payment for the designer

Target Market(s)

real estate investors and building management people

Industry/Entity Type

Law Firm

Font styles to use
Serif

Colors

Designer to choose colors to be used in the design.

Requirements
Must have
• some form of conservative logo

```html
<!DOCTYPE html>
<html lang="en">
<head>
<meta charset="utf-8">
<title>Brandemeier &amp; Brandemeier, LLP — Letterhead</title>
<link href="https://fonts.googleapis.com/css2?family=Libre+Baskerville&family=Arimo:wght@400;700&display=swap" rel="stylesheet">
<style>
  :root {
    --backdrop: #dfe2e4;
    --paper: #ffffff;
    --ink: #3a3f44;
    --ink-soft: #8a8e92;
    --slate-dark: #2e3a45;
    --slate-light: #c9d0d6;
  }
  * { margin: 0; padding: 0; box-sizing: border-box; }
  html, body { width: 1200px; height: 784px; overflow: hidden; background: var(--backdrop); }
  .letterhead {
    position: absolute; left: 330px; top: 12px;
    width: 540px; height: 760px;
    background: var(--paper);
    box-shadow: 0 2px 10px rgba(0,0,0,.12);
    overflow: hidden;
  }
  .corner-accent { position: absolute; width: 46px; }
  .corner-accent--upper {
    right: 0; top: 120px; height: 240px;
    background: linear-gradient(270deg, var(--slate-dark), var(--slate-light));
  }
  .corner-accent--lower {
    left: 0; top: 470px; height: 290px;
    background: linear-gradient(90deg, var(--slate-dark), var(--slate-light));
  }
  .masthead {
    position: absolute; left: 56px; top: 48px;
    display: flex; align-items: flex-start; gap: 34px;
  }
  .firm-name {
    display: flex; align-items: center; gap: 10px;
    font-family: "Libre Baskerville", serif;
    color: var(--slate-dark);
    font-size: 17px; line-height: 1.15; letter-spacing: .5px;
  }
  .firm-name__mark { width: 16px; height: 16px; background: var(--slate-dark); flex: none; }
  .contact {
    list-style: none;
    font-family: "Arimo", sans-serif; font-size: 8px; line-height: 1.55;
    color: var(--ink);
  }
  .contact__address { font-weight: 700; }
  .contact li { display: flex; align-items: flex-start; gap: 5px; }
  .contact__dot { width: 6px; height: 6px; border-radius: 50%; background: var(--ink-soft); margin-top: 2px; flex: none; }
  .contact__dot--blank { background: transparent; }
  .letter-body {
    position: absolute; left: 72px; top: 140px; width: 380px;
    font-family: "Arimo", sans-serif; font-size: 9.5px; line-height: 1.45;
    color: var(--ink-soft);
  }
  .letter-body p { margin-bottom: 14px; }
  .letter-body .indent { text-indent: 40px; }
  .signature {
    position: absolute; left: 250px; top: 500px;
    width: 170px; height: 44px;
    background: linear-gradient(90deg, #f2f3f4, #e9ebec);
    border-radius: 4px;
  }
</style>
</head>
<body>
  <main class="letterhead">
    <div class="corner-accent corner-accent--upper" role="img" aria-label="Decorative slate corner accent"></div>
    <div class="corner-accent corner-accent--lower" role="img" aria-label="Decorative slate corner accent"></div>

    <header class="masthead">
      <div class="firm-name">
        <span class="firm-name__mark"></span>
        <span>BRANDEMEIER &amp;<br>BRANDEMEIER, LLP</span>
      </div>
      <ul class="contact">
        <li class="contact__address"><span class="contact__dot"></span>418 Harbor Lane Suite 210</li>
        <li class="contact__address"><span class="contact__dot contact__dot--blank"></span>Fairhaven, New York 11790</li>
        <li><span class="contact__dot"></span>(555) 014-2290</li>
        <li><span class="contact__dot"></span>(555) 014-3376</li>
        <li><span class="contact__dot"></span>info@brandemeierlaw.com</li>
        <li><span class="contact__dot"></span>www.brandemeierlaw.com</li>
      </ul>
    </header>

    <article class="letter-body">
      <p>Lorem ipsum is simply placeholder text used in printing and typesetting. It has served as standard sample text for a very long time, ever since an unnamed printer took a tray of type and shuffled it to make a specimen book. It has survived not only many decades of print, but also the move into digital typesetting, remaining largely unchanged. It grew popular with sheets of transfer lettering carrying its passages, and later with page layout programs that shipped it as sample copy.</p>
      <p class="indent">It is a long established fact that a reader will be distracted by the readable content of a page when looking at its layout. The point of using lorem ipsum is that it has a more-or-less normal spread of letters, as opposed to repeating 'content here, content here', which makes it look like readable English. Many publishing tools and site editors now use it as their default sample text, and a quick search will uncover many pages still in draft. Various versions have evolved over the years, sometimes by accident, sometimes on purpose.</p>
      <p class="indent">Contrary to popular belief, lorem ipsum is not simply random text. It has roots in a piece of classical Latin writing, making it more than two thousand years old. A retired language scholar at a small northern college looked up one of the more obscure Latin words in a passage, and by tracing its uses through classical literature, found the undoubted source. The passage comes from an old essay on good and evil. Generated lorem ipsum is therefore always free from repetition, injected humour, or out-of-place words.</p>
    </article>

    <div class="signature" role="img" aria-label="Handwritten signature of the sender"></div>
  </main>
</body>
</html>
```